Upmarket Dessert Lounge needs a Business Card Design

We are an upmarket dessert lounge needing a business card to match our image.

We want something that is simple yet beautiful, feminine, classy, sophisticated and elegant. We want it to stand out and don't mind if it is bold.

The design should include our logo and colours of red or maroon with gold highlights. We don't mind if black is used.

Marlow & Quince

Target Market(s)

For those who like to indulge or treat themselves and give in to their temptations on good quality desserts.

Industry/Entity Type

Business

Requirements
Must have
• Must include our logo and our name

Marlow & Quince

M & Q

```html
<!DOCTYPE html>
<html lang="en">
<head>
<meta charset="utf-8">
<title>Marlow &amp; Quince — Business Card</title>
<link rel="stylesheet" href="https://fonts.googleapis.com/css2?family=Cinzel:wght@400&family=Open+Sans:wght@400;700&display=swap">
<style>
  :root {
    --maroon: #7a1416;
    --gold: #f8d3a0;
    --gold-text: #f6dcb4;
    --white: #ffffff;
    --backdrop: #eee8e1;
    --card-w: 511px;
    --card-h: 291px;
    --radius: 22px;
  }
  * { box-sizing: border-box; margin: 0; padding: 0; }
  html, body {
    width: 1200px;
    height: 402px;
    overflow: hidden;
    background: var(--backdrop);
    font-family: "Open Sans", Arial, sans-serif;
  }
  .canvas {
    position: relative;
    width: 1200px;
    height: 402px;
  }
  .card {
    position: absolute;
    top: 56px;
    width: var(--card-w);
    height: var(--card-h);
    border-radius: var(--radius);
    overflow: hidden;
    background: var(--maroon);
    box-shadow: 0 6px 14px rgba(0,0,0,0.25);
  }
  .card--front { left: 64px; }
  .card--back { left: 628px; }

  .front-shape {
    position: absolute;
    inset: 0;
    width: 100%;
    height: 100%;
  }
  .front-shape .panel-white { fill: var(--white); }
  .front-shape .panel-band { fill: var(--gold); }

  .brand-name {
    position: absolute;
    left: 14px;
    top: 90px;
    width: 230px;
    text-align center;
    text-align: center;
    font-family: "Cinzel", Georgia, serif;
    font-weight: 400;
    font-size: 22px;
    color: var(--maroon);
    white-space: nowrap;
  }

  .holder {
    position: absolute;
    left: 27px;
    top: 222px;
    color: var(--maroon);
    font-size: 13px;
  }
  .holder__name {
    font-weight: 700;
    font-size: 16px;
  }

  .address {
    position: absolute;
    right: 33px;
    top: 78px;
    text-align: right;
    font-style: normal;
    color: var(--gold-text);
    font-size: 12.5px;
    line-height: 15px;
  }

  .contact-list {
    position: absolute;
    right: 23px;
    top: 172px;
    list-style: none;
    color: var(--gold-text);
    font-size: 12.5px;
    line-height: 18px;
  }
  .contact-list li {
    display: flex;
    justify-content: flex-end;
    align-items: center;
    gap: 6px;
    white-space: nowrap;
  }
  .contact-list svg {
    width: 11px;
    height: 11px;
    fill: var(--gold-text);
    flex: none;
  }

  .back-mark {
    position: absolute;
    inset: 0;
    display: flex;
    align-items: center;
    justify-content: center;
    font-family: "Cinzel", Georgia, serif;
    font-weight: 400;
    font-size: 84px;
    color: var(--gold);
  }
</style>
</head>
<body>
<main class="canvas">

  <section class="card card--front" aria-label="Business card front">
    <svg class="front-shape" viewBox="0 0 511 291" preserveAspectRatio="none" aria-hidden="true">
      <path class="panel-band" d="M300,0 H322 C360,40 362,115 328,172 C290,236 225,272 160,291 H140 C205,270 265,232 300,172 C335,112 335,40 300,0 Z"/>
      <path class="panel-white" d="M0,0 H300 C335,40 335,112 300,172 C265,232 205,270 140,291 H0 Z"/>
    </svg>

    <div class="brand-name">MARLOW &amp; QUINCE</div>

    <p class="holder"><span class="holder__name">Your name,</span> Title</p>

    <address class="address">
      Street Name<br>
      City Name<br>
      State Zip Code
    </address>

    <ul class="contact-list">
      <li>987-654-3210
        <svg viewBox="0 0 24 24" aria-label="phone"><circle cx="12" cy="12" r="11" fill="none" stroke="#f6dcb4" stroke-width="2"/><path d="M8 6h3l1 3-2 1.5a8 8 0 0 0 3.5 3.5L15 12l3 1v3c-6 1-11-4-10-10z"/></svg>
      </li>
      <li>987-654-3210
        <svg viewBox="0 0 24 24" aria-label="mobile"><path d="M7 1h10a1 1 0 0 1 1 1v20a1 1 0 0 1-1 1H7a1 1 0 0 1-1-1V2a1 1 0 0 1 1-1zm1 3v12h8V4zm4 14a1.5 1.5 0 1 0 0 3 1.5 1.5 0 0 0 0-3z"/></svg>
      </li>
      <li>info@marlow&amp;quince.com
        <svg viewBox="0 0 24 24" aria-label="email"><path d="M1 5h22v14H1zm2 2v.5l9 6 9-6V7z"/></svg>
      </li>
      <li>www.marlow&amp;quince.com
        <svg viewBox="0 0 24 24" aria-label="website"><path d="M12 1a11 11 0 1 0 0 22 11 11 0 0 0 0-22zm0 2c1.2 1.4 2.1 3.5 2.4 6H9.6C9.9 6.5 10.8 4.4 12 3zM7.6 9H3.5a9 9 0 0 1 5.2-5.4A13 13 0 0 0 7.6 9zm0 2a15 15 0 0 0 .1 2H3.2a9 9 0 0 1 0-2zm2 0h4.8a13 13 0 0 1 0 2H9.6a13 13 0 0 1 0-2zm6.8 0h4.4a9 9 0 0 1 0 2h-4.4a15 15 0 0 0 0-2zm0-2a13 13 0 0 0-1.1-5.4A9 9 0 0 1 20.5 9zM3.5 15h4.1a13 13 0 0 0 1.1 5.4A9 9 0 0 1 3.5 15zm6.1 0h4.8c-.3 2.5-1.2 4.6-2.4 6-1.2-1.4-2.1-3.5-2.4-6zm6.8 0h4.1a9 9 0 0 1-5.2 5.4 13 13 0 0 0 1.1-5.4z"/></svg>
      </li>
    </ul>
  </section>

  <section class="card card--back" aria-label="Business card back">
    <div class="back-mark">M &amp; Q</div>
  </section>

</main>
</body>
</html>
```